All-Natural Head Lice Removal company

I need a business card with my pre-existing logo. We are a new company located in Portland Oregon that goes into peoples homes to help with head lice removal. My products and approach are all- natural and also will be around children.On my current logo we used Teal Bl and the color Green. I am open to new ideas just want it simple and creative

Target Market(s)

my biggest market is families of school aged children

Industry/Entity Type

Business

Contact Information for Business Card

see upload for details from previous business card

Font styles to use
Serif

Colors
33a6d7
9bcb3b
f37122

Requirements
Must have
• Basic information/ logo put into a creative format that is catching to the eye
Nice to have
• creative

```html
<!DOCTYPE html>
<html lang="en">
<head>
<meta charset="utf-8">
<title>NitFree Nest – Business Card</title>
<link href="https://fonts.googleapis.com/css2?family=Cabin:wght@400;500;600;700&display=swap" rel="stylesheet">
<style>
  :root {
    --green: #7cc242;
    --teal: #33a6d7;
    --ink: #1e1e1e;
    --paper: #f7f7f7;
    --paper-edge: #e6e6e6;
    --stage: #d9d6d0;
    --muted: #6b6b6b;
  }
  * { margin: 0; padding: 0; box-sizing: border-box; }
  html, body { width: 1200px; height: 1023px; overflow: hidden; }
  body {
    background: var(--stage);
    font-family: "Cabin", sans-serif;
    color: var(--ink);
    position: relative;
  }
  .card {
    position: absolute;
    left: 250px;
    width: 700px;
    height: 400px;
    background: linear-gradient(160deg, #ffffff 0%, var(--paper) 60%, var(--paper-edge) 100%);
    border-radius: 34px;
    overflow: hidden;
    box-shadow: 0 10px 28px rgba(0,0,0,.18);
  }
  .card--front { top: 90px; }
  .card--back { top: 540px; }

  .swoosh { position: absolute; inset: 0; width: 100%; height: 100%; }

  .brand {
    position: absolute;
    display: flex;
    align-items: center;
    gap: 14px;
  }
  .brand__dot {
    width: 74px; height: 74px;
    border-radius: 50%;
    background: var(--green);
    flex: none;
  }
  .brand__name {
    font-weight: 700;
    font-size: 40px;
    color: var(--ink);
    line-height: 1;
    white-space: nowrap;
  }
  .card--front .brand { left: 60px; top: 200px; }

  .headline {
    position: absolute;
    left: 310px; top: 108px;
    width: 350px;
    font-weight: 700;
    font-size: 23px;
    line-height: 1.25;
    color: var(--ink);
  }

  .contact {
    position: absolute;
    right: 44px; top: 168px;
    text-align: right;
  }
  .contact__name {
    font-weight: 700;
    font-size: 22px;
    color: var(--green);
  }
  .contact__role {
    font-weight: 600;
    font-size: 14px;
    color: var(--muted);
    margin-bottom: 8px;
  }
  .contact__line {
    display: flex;
    justify-content: flex-end;
    align-items: center;
    gap: 8px;
    font-size: 15px;
    line-height: 1.6;
    white-space: nowrap;
  }
  .contact__line svg { width: 13px; height: 13px; flex: none; }
  .accent { color: var(--green); }
  .accent-teal { color: var(--teal); }

  .card--back .brand {
    left: 50%; top: 90px;
    transform: translateX(-50%);
  }
  .back-copy {
    position: absolute;
    left: 0; right: 0; top: 220px;
    text-align: center;
    font-size: 20px;
    line-height: 1.45;
  }
</style>
</head>
<body>

<section class="card card--front" aria-label="Card front">
  <svg class="swoosh" viewBox="0 0 700 400" preserveAspectRatio="none" aria-hidden="true">
    <path d="M0,0 H600 C420,12 260,40 190,120 C150,80 80,70 0,110 Z" fill="var(--green)"/>
    <path d="M0,400 V250 C40,340 150,360 260,345 C360,332 450,345 560,400 Z" fill="var(--green)"/>
    <path d="M0,260 C50,345 160,352 265,336 C370,322 470,340 560,400" fill="none" stroke="var(--teal)" stroke-width="16"/>
    <path d="M0,250 C50,330 160,338 262,322 C370,306 480,330 575,400" fill="none" stroke="var(--ink)" stroke-width="9"/>
    <path d="M190,120 C250,70 420,30 620,8" fill="none" stroke="var(--teal)" stroke-width="10"/>
    <path d="M200,132 C260,85 430,42 640,18" fill="none" stroke="var(--ink)" stroke-width="5"/>
  </svg>

  <div class="brand">
    <span class="brand__dot"></span>
    <span class="brand__name">NitFree Nest</span>
  </div>

  <h1 class="headline">All Natural In-Home Lice Removal Services</h1>

  <div class="contact">
    <div class="contact__name">Mara Ellison</div>
    <div class="contact__role">Owner</div>
    <div class="contact__line"><span>1-555-014-NITS (6487)</span>
      <svg viewBox="0 0 16 16"><path d="M3 1 L6 1 L7 5 L5 6 C6 8 8 10 10 11 L11 9 L15 10 L15 13 C15 14 14 15 13 15 C7 15 1 9 1 3 C1 2 2 1 3 1 Z" fill="var(--green)"/></svg>
    </div>
    <div class="contact__line"><span>mara@nitfreenest.com</span>
      <svg viewBox="0 0 16 16"><rect x="1" y="3" width="14" height="10" rx="1.5" fill="var(--green)"/><path d="M1.5 4 L8 9 L14.5 4" fill="none" stroke="#fff" stroke-width="1.3"/></svg>
    </div>
    <div class="contact__line"><span>www.<span class="accent">nitfreenest</span>.com</span>
      <svg viewBox="0 0 16 16"><circle cx="8" cy="8" r="6.5" fill="none" stroke="var(--green)" stroke-width="1.5"/><ellipse cx="8" cy="8" rx="2.8" ry="6.5" fill="none" stroke="var(--green)" stroke-width="1.2"/><line x1="1.5" y1="8" x2="14.5" y2="8" stroke="var(--green)" stroke-width="1.2"/></svg>
    </div>
  </div>
</section>

<section class="card card--back" aria-label="Card back">
  <div class="brand">
    <span class="brand__dot"></span>
    <span class="brand__name">NitFree Nest</span>
  </div>
  <p class="back-copy">
    Try NitFree Nest Today and Be Lice Free Tomorrow!<br>
    All Natural In-Home Lice Removal Servise<br>
    www.<span class="accent-teal">nitfreenest</span>.com
  </p>
</section>

</body>
</html>
```